Bright Wave Labs

We need a professional letter head format for our company. Now we have a logo but need to desing a new logo also. I have uploaded our old logo. Use the color in the logo and design a new one.

Dear Designers , Need to mention "BWL" and please dont use our old LOGO. we need a new catchy one.

```html
<!DOCTYPE html>
<html lang="en">
<head>
<meta charset="utf-8">
<title>Bright Wave Labs – Letterhead</title>
<link href="https://fonts.googleapis.com/css2?family=Lato:wght@400;700&family=Open+Sans:wght@400;600&display=swap" rel="stylesheet">
<style>
  :root {
    --navy: #122d4b;
    --lime: #8cc02f;
    --ink: #3d3d3d;
    --paper: #ffffff;
    --page-bg: #ffffff;
  }
  * { margin: 0; padding: 0; box-sizing: border-box; }
  html, body { width: 1040px; height: 1200px; overflow: hidden; background: var(--page-bg); }
  .letterhead {
    position: relative;
    width: 1040px;
    height: 1200px;
    background: var(--paper);
    font-family: "Open Sans", Arial, sans-serif;
    color: var(--ink);
    overflow: hidden;
  }
  .brand {
    position: absolute;
    right: 107px;
    top: 150px;
    display: flex;
    align-items: center;
    gap: 10px;
  }
  .brand-dot {
    width: 22px; height: 22px;
    border-radius: 50%;
    background: var(--lime);
  }
  .brand-name {
    font-family: "Lato", Arial, sans-serif;
    font-weight: 700;
    font-size: 28px;
    color: var(--navy);
    letter-spacing: 0.2px;
  }
  .letter-body {
    position: absolute;
    left: 99px;
    width: 838px;
    font-size: 15.5px;
  }
  .issue-date { top: 216px; }
  .recipient { top: 253px; line-height: 19px; font-style: normal; }
  .salutation { top: 357px; }
  .content { top: 411px; line-height: 30px; text-align: justify; hyphens: auto; }
  .content p + p { margin-top: 30px; }
  .closing { top: 815px; }
  .signatory { top: 890px; }
  .signatory-name { font-size: 20px; font-weight: 600; color: #333; }
  .signatory-role { margin-top: 4px; font-size: 15.5px; }
  .footer-rule {
    position: absolute;
    left: 0; top: 1076px;
    width: 1040px; height: 7px;
    background: var(--lime);
  }
  .footer-band {
    position: absolute;
    left: 0; top: 1088px;
    width: 1040px; height: 112px;
    background: var(--navy);
  }
  .footer-address {
    position: absolute;
    left: 101px; top: 1149px;
    font-family: "Lato", Arial, sans-serif;
    font-size: 18.5px;
    color: #fff;
  }
  .footer-contacts {
    position: absolute;
    right: 107px; top: 1107px;
    list-style: none;
    font-family: "Lato", Arial, sans-serif;
    font-size: 18.5px;
    color: #fff;
    text-align: right;
    line-height: 23px;
  }
  .footer-contacts li { display: flex; justify-content: flex-end; align-items: center; gap: 5px; }
  .footer-contacts svg { width: 16px; height: 16px; fill: #fff; }
</style>
</head>
<body>
<main class="letterhead">
  <header class="brand">
    <span class="brand-dot"></span>
    <span class="brand-name">Bright Wave Labs</span>
  </header>

  <p class="letter-body issue-date">Issuing Date: May 5, 2018</p>

  <address class="letter-body recipient">
    Name Of Employee Mr. XYZABC<br>
    Address of Employee<br>
    Address Line 2 etc..
  </address>

  <p class="letter-body salutation">Dear Mr.XYZABC</p>

  <section class="letter-body content">
    <p>Lorem Ipsum has been the industry's standard dummy text ever since the 1500s, when an unknown printer took a galley of type and scrambled it to make a type specimen book. It has survived not only five centuries, but also the leap into electronic typesetting, remaining essentially unchanged. It was popularised in the 1960s with the release of Typeline sheets containing Lorem Ipsum passages, and more recently with desktop publishing software like PageCraft including versions of Lorem Ipsum.</p>
    <p>Lorem Ipsum is simply dummy text of the printing and typesetting industry. Lorem Ipsum has been the industry's standard dummy text ever since the 1500s, when an unknown printer took a galley of type and scrambled it to make a type specimen book.</p>
    <p>It has survived not only five centuries, but also the leap into electronic typesetting, remaining essentially unchanged. It was popularised in the 1960s with the release of Typeline sheets containing Lorem IpsumIpsum passages.</p>
  </section>

  <p class="letter-body closing">Yours Sincerely</p>

  <div class="letter-body signatory">
    <p class="signatory-name">Daniel Harper</p>
    <p class="signatory-role">Managing Director</p>
  </div>

  <div class="footer-rule"></div>
  <div class="footer-band"></div>

  <p class="footer-address">88, Harbour Street, 20417, Country Name</p>

  <ul class="footer-contacts">
    <li>044-555 010 220
      <svg viewBox="0 0 16 16"><path d="M3 2h3l1 4-2 1c1 2 2 3 4 4l1-2 4 1v3c0 1-1 1-2 1C6 14 2 10 2 4c0-1 0-2 1-2z"/></svg>
    </li>
    <li>hello@brightwavelabs.com
      <svg viewBox="0 0 16 16"><path d="M1 3h14v10H1z M2 4l6 5 6-5" stroke="var(--navy)" stroke-width="1.2"/></svg>
    </li>
    <li>www.brightwavelabs.com
      <svg viewBox="0 0 16 16"><circle cx="8" cy="8" r="7"/><path d="M1 8h14M8 1c-3 4-3 10 0 14M8 1c3 4 3 10 0 14" stroke="var(--navy)" stroke-width="1.2" fill="none"/></svg>
    </li>
  </ul>
</main>
</body>
</html>
```